I need new business cards designed

I would like to get some new designs on business cards. I will upload my logo for reference. The business cards that were designed for me a few months ago were too difficult for the print companies to work with. My company is Quillbrook.net LLC. It is an art company that sells painting and expression cards online.

```html
<!DOCTYPE html>
<html lang="en">
<head>
<meta charset="utf-8">
<title>Quillbrook.net LLC – Business Cards</title>
<link href="https://fonts.googleapis.com/css2?family=Open+Sans:wght@400;600;700&display=swap" rel="stylesheet">
<style>
  :root {
    --backdrop: #2a2a2a;
    --card: #161616;
    --brand-navy: #3d3b8e;
    --accent-blue: #0ba4df;
    --accent-orange: #f7941d;
    --text-light: #f2f2f2;
  }
  * { margin: 0; padding: 0; box-sizing: border-box; }
  html, body {
    width: 1200px; height: 900px; overflow: hidden;
    background: var(--backdrop);
    font-family: "Open Sans", sans-serif;
  }
  .sheet {
    position: relative; width: 1200px; height: 900px;
    display: flex; align-items: center; justify-content: center; gap: 50px;
  }
  .card {
    position: relative; width: 540px; height: 310px;
    background: var(--card); border-radius: 24px; overflow: hidden;
  }

  /* Front */
  .wave { position: absolute; left: 0; top: 0; width: 540px; height: 310px; }
  .social-row { position: absolute; left: 26px; top: 36px; display: flex; gap: 8px; }
  .social-tile { width: 26px; height: 26px; background: var(--accent-blue); }

  .brand-mark { position: absolute; display: flex; align-items: center; gap: 10px; }
  .brand-mark .brand-square { background: var(--accent-orange); flex: none; }
  .brand-mark .brand-name { color: var(--brand-navy); font-weight: 400; white-space: nowrap; line-height: 1; }
  .card-front .brand-mark { left: 40px; top: 138px; }
  .card-front .brand-square { width: 32px; height: 32px; }
  .card-front .brand-name { font-size: 25px; }

  .divider { position: absolute; left: 272px; top: 78px; width: 1.5px; height: 160px; background: var(--accent-blue); }
  .contact-block { position: absolute; left: 290px; top: 66px; color: var(--text-light); }
  .holder-name { color: var(--accent-blue); font-weight: 700; font-size: 21px; letter-spacing: 0.5px; text-transform: uppercase; line-height: 1.2; }
  .holder-title { font-size: 12.5px; line-height: 1.5; margin-bottom: 6px; }
  .address-line { font-size: 12.5px; line-height: 1.55; }
  .contact-list { list-style: none; margin-top: 6px; }
  .contact-list li { display: flex; align-items: center; gap: 8px; font-size: 12.5px; line-height: 1.65; }
  .contact-list svg { width: 12px; height: 12px; fill: var(--accent-blue); flex: none; }

  /* Back */
  .card-back {
    box-shadow: 0 3px 0 var(--accent-orange), 0 5px 0 #1a1a1a, 0 7px 0 var(--accent-orange), 0 9px 0 #1a1a1a, 0 11px 0 var(--accent-orange);
  }
  .card-back .brand-mark { left: 50%; top: 50%; transform: translate(-50%, -50%); gap: 14px; }
  .card-back .brand-square { width: 56px; height: 56px; }
  .card-back .brand-name { font-size: 40px; }
</style>
</head>
<body>
<main class="sheet">
  <section class="card card-front" aria-label="Business card front">
    <svg class="wave" viewBox="0 0 540 310" aria-hidden="true">
      <path d="M0 310 C140 270 330 290 540 252 L540 310 Z" fill="var(--accent-orange)"/>
      <path d="M0 310 C145 278 335 296 540 259 L540 310 Z" fill="var(--card)"/>
      <path d="M0 310 C150 284 340 300 540 264 L540 310 Z" fill="var(--accent-blue)"/>
    </svg>

    <div class="social-row" aria-label="Social profiles">
      <span class="social-tile"></span>
      <span class="social-tile"></span>
      <span class="social-tile"></span>
    </div>

    <div class="brand-mark">
      <span class="brand-square"></span>
      <span class="brand-name">Quillbrook.net</span>
    </div>

    <span class="divider"></span>

    <div class="contact-block">
      <h1 class="holder-name">Mara Ellison</h1>
      <p class="holder-title">Managing Director</p>
      <p class="address-line">Your address, City</p>
      <p class="address-line">State, Zip 1234</p>
      <ul class="contact-list">
        <li><svg viewBox="0 0 12 12"><path d="M2 1h2.5l1 2.8-1.4 1a6 6 0 0 0 3.1 3.1l1-1.4 2.8 1V10a1 1 0 0 1-1 1A9 9 0 0 1 1 2a1 1 0 0 1 1-1z"/></svg>555-214-0387</li>
        <li><svg viewBox="0 0 12 12"><path d="M1 2.5h10v7H1z M1 2.5l5 4 5-4" fill="none" stroke="var(--accent-blue)" stroke-width="1.3"/></svg>info@quillbrook.net</li>
        <li><svg viewBox="0 0 12 12"><circle cx="6" cy="6" r="5" fill="none" stroke="var(--accent-blue)" stroke-width="1.2"/><path d="M1 6h10M6 1c-2.5 3-2.5 7 0 10M6 1c2.5 3 2.5 7 0 10" fill="none" stroke="var(--accent-blue)" stroke-width="1"/></svg>www.Quillbrook.net</li>
      </ul>
    </div>
  </section>

  <section class="card card-back" aria-label="Business card back">
    <div class="brand-mark">
      <span class="brand-square"></span>
      <span class="brand-name">Quillbrook.net</span>
    </div>
  </section>
</main>
</body>
</html>
```